BrivoTerna. Lantern of the Steady Harvest. Business card

Professional business card for BrivoTerna (Lantern of the Steady Harvest)
My rationale: Strategy-> Execution-> Results-> Value that lead to the BrivoTerna name: We put the Lantern of the Steady Harvest.
We deliver value to our customers helping them at defining a good strategy (cyan arrow). 90% of well formulated strategies fail due to poor execution so we also consider strategical execution very important (green arrow). Due to the execution we obtain the results (blue arrow). Finally, the results provide feedback to redefine strategy, and the new strategy has to be executed and new results obtained providing new feedback and on and on. It's like a wheel that finally, must create corporate value: value for shareholders, staholders, employees, providers...-

Target Market(s)

CEOs and steering comitees , invewrnent funds

Industry/Entity Type

Business Consultant

Contact Information for Business Card

Teodoro Vinsquel
CEO & Founder
teodoro.vinsquel@brivoterna-example.com
Mobile: +34 655.803.912
www.brivoterna-example.com

Colors

Designer to choose colors to be used in the design.

Requirements
Nice to have
• Nice to hace the words: Strategy, execution, results
• Nice to vave the claim: Lantern of the Steady Harvest
• The three colors should be shown:
• cyan for STRATEGY
• green for EXECUTION
• blue for RESULTS
Should not have
• Complete black background

```html
<!DOCTYPE html>
<html lang="en">
<head>
<meta charset="utf-8">
<title>BrivoTerna – Business Card</title>
<link rel="stylesheet" href="https://fonts.googleapis.com/css2?family=Arimo:wght@400;700&display=swap">
<style>
  :root {
    --bg: #e4e6ea;
    --royal: #0b4ea2;
    --cyan: #10a8e8;
    --navy: #1b2c8e;
    --green: #98c83a;
    --white: #ffffff;
    --grey: #4a4f57;
  }
  * { box-sizing: border-box; margin: 0; padding: 0; }
  html, body {
    width: 1200px; height: 1015px; overflow: hidden;
    background: var(--bg);
    font-family: "Arimo", Arial, sans-serif;
  }
  .sheet {
    width: 1200px; height: 1015px;
    display: flex; flex-direction: column; align-items: center;
    justify-content: center; gap: 22px;
  }
  .card {
    position: relative; width: 820px; height: 470px; overflow: hidden;
    box-shadow: 0 6px 18px rgba(0,0,0,.18);
  }

  /* Front */
  .card-front { background: var(--royal); }
  .front-brand {
    position: absolute; left: 0; right: 0; top: 150px;
    text-align: center; color: var(--white);
    font-weight: 700; font-size: 76px; letter-spacing: -1px;
    display: flex; align-items: center; justify-content: center; gap: 18px;
  }
  .front-brand .dot { width: 26px; height: 26px; border-radius: 50%; background: var(--white); }
  .front-band {
    position: absolute; left: 0; right: 0; top: 298px; height: 62px;
    background: var(--cyan);
    display: flex; align-items: center; justify-content: center;
  }
  .tagline {
    color: var(--white); font-size: 19px; letter-spacing: 1.5px; text-transform: uppercase;
  }

  /* Back */
  .card-back { background: var(--white); }
  .back-brand {
    position: absolute; right: 70px; top: 92px;
    color: var(--navy); font-weight: 700; font-size: 52px; letter-spacing: -1px;
  }
  .holder { position: absolute; left: 60px; top: 132px; }
  .holder-name { color: var(--navy); font-size: 28px; }
  .holder-role { color: var(--grey); font-size: 17px; margin-top: 3px; }
  .contacts {
    position: absolute; left: 60px; top: 250px;
    list-style: none; color: var(--grey); font-size: 18px;
  }
  .contacts li { display: flex; align-items: center; gap: 10px; line-height: 25px; }
  .contacts svg { width: 17px; height: 17px; fill: var(--navy); flex: none; }
  .back-band {
    position: absolute; left: 0; right: 0; bottom: 0; height: 142px;
    background: var(--green);
    display: flex; align-items: center; justify-content: center;
  }
  .motto { color: var(--white); font-size: 22px; letter-spacing: 1.5px; text-transform: uppercase; }
</style>
</head>
<body>
<main class="sheet">
  <section class="card card-front" aria-label="Business card front">
    <div class="front-brand"><span class="dot" aria-hidden="true"></span>BrivoTerna</div>
    <div class="front-band"><p class="tagline">Lantern of the Steady Harvest</p></div>
  </section>

  <section class="card card-back" aria-label="Business card back">
    <div class="back-brand">BrivoTerna</div>
    <div class="holder">
      <p class="holder-name">Teodoro Vinsquel</p>
      <p class="holder-role">CEO &amp; Founder</p>
    </div>
    <ul class="contacts">
      <li>
        <svg viewBox="0 0 24 24" aria-hidden="true"><path d="M6.6 10.8a15 15 0 0 0 6.6 6.6l2.2-2.2a1 1 0 0 1 1-.25 11.4 11.4 0 0 0 3.6.57 1 1 0 0 1 1 1V20a1 1 0 0 1-1 1A17 17 0 0 1 3 4a1 1 0 0 1 1-1h3.5a1 1 0 0 1 1 1c0 1.25.2 2.45.57 3.57a1 1 0 0 1-.25 1z"/></svg>
        +34 655.803.912
      </li>
      <li>
        <svg viewBox="0 0 24 24" aria-hidden="true"><path d="M2 5h20v14H2zm2 2v.4l8 5.2 8-5.2V7zm0 2.8V17h16V9.8l-8 5.2z"/></svg>
        teodoro.vinsquel@brivoterna-example.com
      </li>
      <li>
        <svg viewBox="0 0 24 24" aria-hidden="true"><circle cx="12" cy="12" r="10"/><path d="M2 12h20M12 2c3 3 3 17 0 20M12 2c-3 3-3 17 0 20" stroke="#fff" stroke-width="1.4" fill="none"/></svg>
        www.brivoterna-example.com
      </li>
    </ul>
    <div class="back-band"><p class="motto">Strategy, Execution, Results</p></div>
  </section>
</main>
</body>
</html>
```